Business card design for my company.
I would like the card's background colour to be black. You can also see our web site to get an idea of our brand. https://www.tmwhomecrafting.com.au/
- Name
- Email

```html
<!DOCTYPE html>
<html lang="en">
<head>
<meta charset="utf-8">
<title>TMW Home Crafting – Business Card</title>
<link href="https://fonts.googleapis.com/css2?family=Open+Sans:wght@400;700&display=swap" rel="stylesheet">
<style>
  :root {
    --bg: #1e1e1f;
    --card-black: #141414;
    --brand-green: #18993a;
    --paper-white: #f7f7f7;
    --text-white: #ffffff;
    --text-dark: #2a2a2a;
    --muted: #d6d6d6;
  }
  html, body {
    margin: 0;
    padding: 0;
    width: 1200px;
    height: 1088px;
    overflow: hidden;
    background: var(--bg);
    font-family: "Open Sans", Arial, sans-serif;
  }
  .canvas {
    position: relative;
    width: 1200px;
    height: 1088px;
  }
  .card {
    position: absolute;
    width: 620px;
    height: 379px;
    border-radius: 4px;
    overflow: hidden;
    background: var(--card-black);
    box-shadow: 0 18px 40px rgba(0,0,0,0.45);
  }
  .card-front { left: 80px; top: 90px; }
  .card-back  { left: 500px; top: 620px; }

  .front-shapes { position: absolute; inset: 0; }

  .person {
    position: absolute;
    left: 40px;
    top: 120px;
  }
  .person-name {
    margin: 0;
    font-size: 21px;
    font-weight: 700;
    color: var(--brand-green);
    letter-spacing: 0.3px;
  }
  .person-role {
    margin: 2px 0 0;
    font-size: 15px;
    color: var(--text-dark);
  }

  .brand-name {
    position: absolute;
    right: 34px;
    top: 96px;
    margin: 0;
    font-size: 24px;
    font-weight: 700;
    letter-spacing: 2px;
    color: var(--text-white);
    text-align: right;
    line-height: 1.15;
  }
  .location {
    position: absolute;
    right: 34px;
    top: 186px;
    margin: 0;
    font-size: 14px;
    color: var(--muted);
    text-align: right;
    line-height: 1.35;
  }

  .contact {
    position: absolute;
    left: 200px;
    bottom: 34px;
    margin: 0;
    padding: 0;
    list-style: none;
    font-size: 14px;
    color: var(--text-white);
    line-height: 1.55;
  }
  .contact li { display: flex; align-items: center; gap: 8px; }
  .contact svg { width: 12px; height: 12px; fill: var(--brand-green); flex: none; }

  .back-brand {
    position: absolute;
    inset: 0;
    display: flex;
    align-items: center;
    justify-content: center;
    margin: 0;
    font-size: 40px;
    font-weight: 700;
    letter-spacing: 6px;
    color: var(--text-white);
  }
</style>
</head>
<body>
<main class="canvas">

  <section class="card card-front" aria-label="Business card front">
    <svg class="front-shapes" viewBox="0 0 620 379" width="620" height="379" aria-hidden="true">
      <polygon class="paper-area" points="0,0 620,0 620,14 440,14 70,379 0,379" fill="var(--paper-white)"/>
      <polygon class="green-band" points="440,14 620,14 620,40 470,40 112,379 70,379" fill="var(--brand-green)"/>
    </svg>

    <div class="person">
      <p class="person-name">MARCUS HALE</p>
      <p class="person-role">Managing Director</p>
    </div>

    <p class="brand-name">TMW<br>HOME CRAFTING</p>
    <p class="location">Devonport, Tasmania<br>Australia</p>

    <ul class="contact">
      <li>
        <svg viewBox="0 0 24 24"><path d="M6.6 10.8a15.1 15.1 0 0 0 6.6 6.6l2.2-2.2a1 1 0 0 1 1-.25 11.4 11.4 0 0 0 3.6.57 1 1 0 0 1 1 1V20a1 1 0 0 1-1 1A17 17 0 0 1 3 4a1 1 0 0 1 1-1h3.5a1 1 0 0 1 1 1c0 1.25.2 2.45.57 3.57a1 1 0 0 1-.25 1z"/></svg>
        0400 123 456
      </li>
      <li>
        <svg viewBox="0 0 24 24"><path d="M2 5h20v14H2z M4 7v.5l8 5 8-5V7l-8 5z"/></svg>
        info@tmwhomecrafting.com.au
      </li>
      <li>
        <svg viewBox="0 0 24 24"><circle cx="12" cy="12" r="10"/></svg>
        www.tmwhomecrafting.com.au
      </li>
    </ul>
  </section>

  <section class="card card-back" aria-label="Business card back">
    <p class="back-brand">TMW HOME CRAFTING</p>
  </section>

</main>
</body>
</html>
```